WordPress Design (redesign) and Coding for Funeral Consulting Services & mobile app

I need an attractive SEO friendly WordPress design.

Incorporating all of the latest design standards in a graceful and appealing way. I'd like to see CTA's for for funeral consulting services. People should be able to purchase my consulting services directly from the website so I'd like to see nice buttons.

Funeral Consulting Services are the main topic for this website.

I also have an iOS app called Velomarque in the iOS Appvault Shelf. I want buttons and CTAs so that users can download the app right to their iOS device(s). Make this a secondary focus.

I want more of a mobile focus as that is where I expect the most traffic. Mobile users like to act quickly and they also like to scroll if their interest is captured so I want the design to reflect that.

End to end design
Large Creative Typography for increased mobile searchers.
attractive CTA’s
RGB Vivid / Bright Colors that match our logo
A menu that is easy to find and use on mobile devices
button(s) for iOS app download.

the current website is www.velomarque-example.com This website was a placeholder.
Updates

I'd need users to fill out a survey so that I may collect information from them to better provide service to them.

reference websites: Quillvant.com & Torbex.com for website design inspiratioin. reference Harnwick.com for blog

Target Market(s)

18-35 year old mobile users

Industry/Entity Type

Consulting

Coding

Coded - Design and coding required

Font styles to use
Sans Serif

Colors
fbee3d
000000
ffffff
cbcbcb
fefdec

Requirements
Must have
• iOS app logo and iOS app logo colors should have its own area/page
• CTA's for consulting services and app download. Main topic
• reviews (testimonials)
• Video area
• end to end design
• creative typography
Nice to have
• a beautiful blog page that blends well with the design
Should not have
• Any imagery related to funerals or burials.

```html
<!DOCTYPE html>
<html lang="en">
<head>
<meta charset="utf-8">
<title>Velomarque — Funeral Consulting Services</title>
<link href="https://fonts.googleapis.com/css2?family=Open+Sans:wght@400;600;700&family=Roboto:wght@400;500;700&family=Lobster&display=swap" rel="stylesheet">
<style>
:root{
  --yellow:#fbee3d;
  --btn-top:#fcd22a;
  --btn-bottom:#eaa500;
  --black:#000000;
  --white:#ffffff;
  --grey:#cbcbcb;
  --cream:#fefdec;
  --ink:#333333;
  --muted:#666666;
  --panel:#ebebeb;
  --dark:#2f2f2f;
}
*{box-sizing:border-box;margin:0;padding:0}
html,body{width:1200px;height:4276px;overflow:hidden}
body{font-family:"Open Sans",sans-serif;color:var(--ink);background:var(--white);position:relative}
.section{position:absolute;left:0;width:1200px}
h2,h3{font-family:"Roboto",sans-serif}
.btn{display:inline-flex;align-items:center;gap:8px;padding:0 24px;height:46px;border:2px solid #2b2b2b;border-radius:4px;
  background:linear-gradient(var(--btn-top),var(--btn-bottom));color:#1a1a1a;font:600 16px "Roboto",sans-serif;
  box-shadow:0 6px 8px rgba(0,0,0,.35)}
.body-text{font-size:12px;line-height:21px;color:var(--muted)}

/* header */
.site-header{top:0;height:80px;background:var(--white);z-index:3}
.brand{position:absolute;left:100px;top:0;width:250px;height:120px;background:var(--white);border-radius:0 0 125px 125px / 0 0 40px 40px;
  display:flex;align-items:center;justify-content:center;font:700 34px "Roboto",sans-serif;color:var(--black)}
.brand-wrap{position:absolute;left:100px;top:0;height:80px;display:flex;align-items:center;gap:10px;font:700 34px "Roboto",sans-serif;color:var(--black)}
.brand-dot{width:16px;height:16px;border-radius:50%;background:var(--yellow);border:2px solid var(--black)}
.call{position:absolute;right:100px;top:12px;font:700 14px "Roboto",sans-serif;color:var(--black)}
.main-nav{position:absolute;right:100px;top:42px;display:flex;gap:32px;font:500 15px "Roboto",sans-serif;color:#222}
.main-nav .active{border-bottom:2px solid var(--yellow);padding-bottom:4px}

/* hero */
.hero{top:80px;height:476px;background:linear-gradient(180deg,#4f7fb8 0%,#7ea4cf 45%,#b9cde4 80%,#e3ebf4 100%);text-align:center;color:var(--white)}
.hero h1{font:700 36px "Roboto",sans-serif;margin-top:130px;text-shadow:0 2px 4px rgba(0,0,0,.3)}
.hero p{font:600 16px/26px "Open Sans",sans-serif;width:980px;margin:16px auto 20px}
.dots{position:absolute;left:0;right:0;bottom:20px;display:flex;justify-content:center;gap:6px}
.dots i{width:10px;height:10px;border-radius:50%;border:1px solid var(--white)}
.dots i:first-child{background:var(--white)}

/* about */
.about{top:556px;height:556px}
.about h2{position:absolute;left:100px;top:100px;font-size:28px;color:#333}
.about h3{position:absolute;left:100px;top:150px;width:540px;font-size:20px;font-weight:500;line-height:28px;color:#444}
.rule{position:absolute;height:2px;width:90px;background:var(--yellow)}
.about .body-text{position:absolute;left:100px;top:236px;width:540px}
.about .btn{position:absolute;left:100px;top:390px}
.about .photo{position:absolute;left:715px;top:80px;width:385px;height:404px;background:linear-gradient(135deg,#dfe3e2,#a9a59a 55%,#6f6a63)}

/* quote band */
.quote-band{top:1112px;height:313px;background:linear-gradient(90deg,#4a4a4a,#6e6e6e 50%,#3e3e3e);text-align:center;color:var(--white)}
.quote-band p{font:400 24px/36px "Open Sans",sans-serif;width:900px;margin:78px auto 30px}

/* process */
.process{top:1425px;height:479px}
.player{position:absolute;left:100px;top:85px;width:455px;height:290px;background:var(--white);border:6px solid #222;border-radius:4px;overflow:hidden}
.player .bar{position:absolute;left:0;right:0;height:22px;background:#2b2b2b}
.player .top{top:0}.player .bottom{bottom:0}
.player .title{position:absolute;left:0;right:0;top:110px;text-align:center;font:700 52px "Roboto",sans-serif;color:var(--black)}
.player svg{position:absolute;left:193px;top:112px}
.more{position:absolute;left:100px;top:386px;width:455px;text-align:center;font:700 11px "Roboto",sans-serif;text-decoration:underline;color:#222}
.process h2{position:absolute;left:630px;top:82px;font-size:26px;color:#333}
.process .body-text{position:absolute;left:630px;top:126px;width:470px;line-height:20px}
.process .btn{position:absolute;left:630px;top:330px}

/* planning */
.planning{top:1904px;height:313px;background:linear-gradient(90deg,#c9c79a,#dedcb8 40%,#cfcfa2 70%,#b9b78a);text-align:center;color:var(--white)}
.planning h2{font-size:28px;margin-top:84px;text-shadow:0 1px 3px rgba(0,0,0,.3)}
.planning p{font-size:16px;line-height:24px;width:820px;margin:10px auto 22px;text-shadow:0 1px 2px rgba(0,0,0,.35)}

/* blog */
.blog{top:2217px;height:533px}
.blog > h2{text-align:center;font-size:28px;color:#333;margin-top:68px}
.card{position:absolute;top:153px;width:318px}
.card .thumb{height:225px;border-radius:10px;position:relative}
.date{position:absolute;right:0;top:0;width:74px;height:74px;background:var(--yellow);border-radius:0 10px 0 0;text-align:center;font:700 18px/22px "Roboto",sans-serif;color:#222;padding-top:14px}
.card h3{font-size:18px;font-weight:500;margin-top:24px;color:#222}
.meta{display:flex;gap:26px;margin-top:14px;font-size:14px;color:#555}
.meta span::before{content:"";display:inline-block;width:10px;height:10px;background:#e0b400;border-radius:50%;margin-right:8px}

/* app */
.app{top:2750px;height:550px;background:var(--panel);overflow:hidden}
.ghost{position:absolute;left:300px;top:450px;font:400 64px "Open Sans",sans-serif;color:rgba(0,0,0,.06);white-space:nowrap}
.app h2{position:absolute;left:100px;top:110px;font-size:28px;color:#333}
.app h3{position:absolute;left:100px;top:158px;width:480px;font-size:22px;font-weight:500;line-height:30px;color:#444}
.app .body-text{position:absolute;left:100px;top:250px;width:560px}
.app .btn{position:absolute;left:100px;top:398px}
.phone{position:absolute;left:805px;top:82px;width:198px;height:408px;background:#111;border-radius:30px;box-shadow:0 10px 20px rgba(0,0,0,.3)}
.screen{position:absolute;left:12px;top:58px;width:174px;height:290px;background:linear-gradient(180deg,#fbfbf6 0 32%,#a6b35e 32%,#6f8a35);text-align:center}
.screen .name{font:700 24px "Roboto",sans-serif;color:var(--black);padding-top:34px}
.screen .tag{font-size:8px;color:#333}
.screen .bt{width:120px;height:18px;margin:10px auto 0;background:#222;border-radius:3px;font-size:8px;line-height:18px;color:var(--white)}
.screen .bt:first-of-type{margin-top:120px}
.home{position:absolute;left:84px;bottom:18px;width:30px;height:30px;border-radius:50%;border:2px solid #444}

/* consultant band */
.consult{top:3300px;height:234px;background:linear-gradient(90deg,#4d4a3e,#6d6a5a 50%,#454238)}
.consult p{position:absolute;left:100px;top:80px;width:780px;font:600 15px/25px "Open Sans",sans-serif;color:var(--white)}
.consult .btn{position:absolute;left:875px;top:86px}

/* testimonials */
.testimonials{top:3534px;height:479px}
.testimonials > h2{text-align:center;font-size:28px;color:#333;margin-top:58px}
.quote{position:absolute;top:135px;width:318px;height:140px;background:var(--white);border-radius:10px;box-shadow:0 4px 14px rgba(0,0,0,.2);padding:34px 30px;text-align:center;font-size:11px;line-height:19px;color:#555}
.person{position:absolute;top:315px;display:flex;align-items:center;gap:20px}
.avatar{width:66px;height:66px;border-radius:50%}
.person b{display:block;font:700 17px "Roboto",sans-serif;color:#222}
.person small{font-size:11px;color:#666}

/* footer */
.site-footer{top:4013px;height:263px;background:linear-gradient(90deg,#1c1c1c,#2a2a2a 60%,#1a1a1a);color:var(--white)}
.badge{position:absolute;left:100px;top:60px;width:100px;height:100px;border-radius:50%;border:3px solid var(--yellow);background:#111;display:flex;align-items:center;justify-content:center;font:700 15px "Roboto",sans-serif;color:var(--white)}
.f-about{position:absolute;left:268px;top:50px;width:260px}
.site-footer h4{font:700 16px "Roboto",sans-serif;margin-bottom:10px}
.f-about p{font-size:11px;line-height:18px;color:#ddd}
.f-sub{position:absolute;left:608px;top:50px}
.f-sub .field{width:260px;height:30px;border:1px solid #bbb;font-size:11px;line-height:28px;padding-left:8px;color:#ccc}
.f-sub .go{margin-top:14px;width:96px;height:26px;border:1px solid #222;background:linear-gradient(var(--btn-top),var(--btn-bottom));color:#222;font:600 11px/24px "Roboto",sans-serif;text-align:center}
.f-follow{position:absolute;left:958px;top:50px}
.icons{display:flex;gap:16px;margin-top:8px}
.icons i{width:14px;height:14px;border-radius:50%;background:var(--white)}
.copy{position:absolute;left:0;right:0;bottom:14px;text-align:center;font-size:11px;color:#ccc}
</style>
</head>
<body>

<header class="section site-header">
  <div class="brand-wrap"><span class="brand-dot"></span>Velomarque</div>
  <div class="call">Call : +1 800 555 0142</div>
  <nav class="main-nav">
    <span class="active">Home</span><span>About</span><span>Planning</span><span>Services</span><span>Obituaries</span><span>Resources</span>
    <svg width="14" height="14" viewBox="0 0 14 14"><circle cx="6" cy="6" r="4.5" fill="none" stroke="#222" stroke-width="2"/><line x1="9.5" y1="9.5" x2="13" y2="13" stroke="#222" stroke-width="2"/></svg>
  </nav>
</header>

<section class="section hero" role="img" aria-label="Soft blue sky with drifting clouds">
  <h1>We're here to help you through this difficult time</h1>
  <p>We guide families through every choice with calm advice, honest pricing and a plan that fits your wishes and your budget.</p>
  <span class="btn">Search For Location
    <svg width="14" height="14" viewBox="0 0 14 14"><circle cx="6" cy="6" r="4.5" fill="none" stroke="#1a1a1a" stroke-width="2"/><line x1="9.5" y1="9.5" x2="13" y2="13" stroke="#1a1a1a" stroke-width="2"/></svg>
  </span>
  <div class="dots"><i></i><i></i><i></i><i></i></div>
</section>

<section class="section about">
  <h2>About Us</h2>
  <h3>We Are Giving the Best Quality And Traditional Services</h3>
  <div class="rule" style="left:100px;top:222px"></div>
  <div class="body-text">
    <p>Funerals are expensive. Having to finance one suddenly can be a burden to many families, especially those that are uninsured or unprepared. Not coincidentally, there is often a windfall of money at this time, in the form of donations, family contributions, and life insurance proceeds. Families tend to consider this money 'going away' funds.</p>
    <p style="margin-top:12px">The funeral industry wants to pressure you into spending your last dollar on that event.</p>
  </div>
  <span class="btn">Don't Throw Money Away</span>
  <div class="photo" role="img" aria-label="Photo of two men talking warmly at home"></div>
</section>

<section class="section quote-band" role="img" aria-label="Muted dark background photo">
  <p>The fact is, life insurance was never intended to be fully used on a fancy funeral, but rather as a hedge against disaster for the survivors</p>
  <span class="btn">Save Money Now</span>
</section>

<section class="section process">
  <div class="player">
    <div class="bar top"></div>
    <div class="title">Velomarque</div>
    <svg width="48" height="48" viewBox="0 0 48 48"><circle cx="24" cy="24" r="23" fill="#555"/><path d="M19 14 L35 24 L19 34 Z" fill="#fbee3d"/></svg>
    <div class="bar bottom"></div>
  </div>
  <div class="more">Watch More Videos</div>
  <h2>Our Working Process</h2>
  <div class="body-text">
    <p>The first step in funeral planning, particularly if you find yourself in need, is to get a friend by your side. This should be someone who is somewhat removed from the deceased, so the friend's emotions will not be a factor. It should also be someone whose judgement you trust and, preferably, someone who has been through the arrangement process in the recent past.</p>
    <p style="margin-top:12px">This friend should be someone who has the strength of character to say 'NO' or at least 'Not YET', to keep you from being pressured into hasty, expensive financial decisions.</p>
  </div>
  <span class="btn">Save Money Today</span>
</section>

<section class="section planning" role="img" aria-label="Soft green background of pale blossoms">
  <h2>Planning Ahead</h2>
  <p>In a survey of several thousand funeral directors, in response to the question 'Why would you say funerals cost so much?' over 85% replied "Emotional overspending by the family."</p>
  <span class="btn">Get Help Now !</span>
</section>

<section class="section blog">
  <h2>Our Blog</h2>
  <article class="card" style="left:100px">
    <div class="thumb" role="img" aria-label="Candle glowing beside white flowers" style="background:linear-gradient(135deg,#3a2a18,#a8742a 45%,#d9d4c6 80%)">
      <div class="date">28<br>Dec</div>
    </div>
    <h3>Lorem Ipsum Is Simply dummy</h3>
    <div class="meta"><span>Arlo Venn</span><span>4 Comments</span></div>
  </article>
  <article class="card" style="left:441px">
    <div class="thumb" role="img" aria-label="White figurine beside a red rose on wood" style="background:linear-gradient(135deg,#7a5a3e,#d8d2c6 45%,#a0302a 80%,#5b3a24)">
      <div class="date">28<br>Dec</div>
    </div>
    <h3>Lorem Ipsum Is Simply dummy</h3>
    <div class="meta"><span>Arlo Venn</span><span>4 Comments</span></div>
  </article>
  <article class="card" style="left:782px">
    <div class="thumb" role="img" aria-label="Sunlit green garden path under trees" style="background:linear-gradient(135deg,#2f4a1e,#7aa04a 50%,#c9d89a)">
      <div class="date">28<br>Dec</div>
    </div>
    <h3>Lorem Ipsum Is Simply dummy</h3>
    <div class="meta"><span>Arlo Venn</span><span>4 Comments</span></div>
  </article>
</section>

<section class="section app">
  <div class="ghost">Tribute Your Decoration</div>
  <h2>Download Our App</h2>
  <h3>I don't think I need anything else right now... who else feels the same?</h3>
  <div class="body-text">
    <p>Funerals are expensive. Having to finance one suddenly can be a burden to many families, especially those that are uninsured or unprepared. Not coincidentally, there is often a windfall of money at this time, in the form of donations, family contributions, and life insurance proceeds. Families tend to consider this money 'going away' funds.</p>
    <p style="margin-top:12px">The funeral industry wants to pressure you into spending your last dollar on that event.</p>
  </div>
  <span class="btn">Download our App Now</span>
  <div class="phone">
    <div class="screen">
      <div class="name">Velomarque</div>
      <div class="tag">Tribute Your Decoration</div>
      <div class="bt">SIGN IN</div>
      <div class="bt">SIGN UP</div>
    </div>
    <div class="home"></div>
  </div>
</section>

<section class="section consult" role="img" aria-label="Dim background photo in warm grey tones">
  <p>A funeral consultant is someone who, on their own, goes out and does all the things related to making funeral arrangements.However we do so with your budget and your ideals in mind. We represent you as your spokesperson and friend during this tough time.</p>
  <span class="btn">Get Help ASAP</span>
</section>

<section class="section testimonials">
  <h2>Testimonials</h2>
  <div class="quote" style="left:100px">They listened first and planned second. Our family stayed calm, on budget and cared for through every single step.</div>
  <div class="quote" style="left:441px">Clear advice, kind words and no pressure at all. I would ask them again without a second thought.</div>
  <div class="quote" style="left:782px">They saved us money and stress at once, and stayed close by until the very last detail was done.</div>
  <div class="person" style="left:110px"><div class="avatar" role="img" aria-label="Client portrait" style="background:#3a3a3a"></div><div><b>Dorian Fellowes</b><small>Our Client</small></div></div>
  <div class="person" style="left:451px"><div class="avatar" role="img" aria-label="Client portrait" style="background:#c9a98a"></div><div><b>Sarita Vale</b><small>Our Client</small></div></div>
  <div class="person" style="left:792px"><div class="avatar" role="img" aria-label="Client portrait" style="background:#8a9bb0"></div><div><b>Jonah Pell</b><small>Our Client</small></div></div>
</section>

<footer class="section site-footer">
  <div class="badge">Velomarque</div>
  <div class="f-about">
    <h4>About</h4>
    <p>Honest funeral guidance for families who want calm, clear choices and a plan that respects both their wishes and budget.</p>
  </div>
  <div class="f-sub">
    <h4>Subscribe Newsletter</h4>
    <div class="field">Enter the Email</div>
    <div class="go">Subscribe</div>
  </div>
  <div class="f-follow">
    <h4>Follow Us On</h4>
    <div class="icons"><i></i><i></i><i></i><i></i></div>
  </div>
  <div class="copy">© 2017. All Rights Reserved.</div>
</footer>

</body>
</html>
```